Business Cards Needed for Innovative Healthcare Marketing Company

We are a marketing company focused on healthcare. Our company is all about rebranding yourself renewing your image and generating results. The phoenix stands for "reborn" or "rising" which we provide new brands for our clients we take their old brands and renew it with creativity and innovation. I am looking for a business card with color dimension. I have attached an example of a card I think has the look and feel of what I am trying to accomplish. I like that the card example has black and grey font colors, I like the font placement and the small logo, I really like the use of the colors on the right those are the colors of my logo. My logo is phoenix so maybe incorporating flames similar to that design. I would like the back a solid color maybe red with an opaque version of the logo and website. As a marketing company I am always open to creative liberty!

Target Market(s)

Doctors and business professionals.

Industry/Entity Type

Marketing

Contact Information for Business Card

Valcorne Health Care Marketing
Marla Tenwick- CEO
#(512)638-2974
email-marla@valcorne.com
website- valcorne.com

Font styles to use
Sans Serif

Colors
ec1f27
f37122
ffc214
fbed22
fbf289
f04a50

Requirements
Must have
• The logo and required information
Nice to have
• icons by the information
Should not have
• child like font

```html
<!DOCTYPE html>
<html lang="en">
<head>
<meta charset="utf-8">
<title>Valcorne Health Care Marketing – Business Cards</title>
<link rel="stylesheet" href="https://fonts.googleapis.com/css2?family=Arimo:wght@400;500&display=swap">
<style>
  :root {
    --canvas: #e9e9e9;
    --card: #ffffff;
    --brand-red: #a3201f;
    --brand-orange: #f08a24;
    --ink: #111111;
    --glow-top: #e9ad98;
    --glow-mid: #f6c6a0;
    --glow-bottom: #fde3b0;
  }
  * { box-sizing: border-box; margin: 0; padding: 0; }
  html, body {
    width: 1189px;
    height: 1200px;
    overflow: hidden;
    background: var(--canvas);
    font-family: "Arimo", Arial, sans-serif;
  }
  .card {
    position: absolute;
    left: 194px;
    width: 807px;
    height: 460px;
    background: var(--card);
    box-shadow: 0 3px 8px rgba(0,0,0,0.35);
  }
  .card--front { top: 111px; }
  .card--back { top: 620px; }

  .brand {
    position: absolute;
    display: flex;
    align-items: center;
    gap: 14px;
  }
  .brand__dot {
    width: 30px;
    height: 30px;
    border-radius: 50%;
    background: var(--brand-orange);
    flex: none;
  }
  .brand__text {
    display: flex;
    flex-direction: column;
    color: var(--brand-red);
    font-weight: 400;
    white-space: nowrap;
  }
  .brand__name {
    font-size: 46px;
    line-height: 46px;
    letter-spacing: 2px;
  }
  .brand__rule {
    height: 1px;
    margin: 8px 0 6px;
    background: var(--brand-red);
  }
  .brand__tagline {
    font-size: 15px;
    line-height: 18px;
    letter-spacing: 1.4px;
  }
  .card--front .brand { left: 56px; top: 186px; }
  .card--back .brand { left: 476px; top: 318px; }

  .divider {
    position: absolute;
    left: 400px;
    top: 65px;
    width: 2px;
    height: 330px;
    background: var(--brand-red);
  }
  .person {
    position: absolute;
    left: 477px;
    top: 92px;
    color: var(--ink);
  }
  .person__name { font-size: 24px; line-height: 30px; }
  .person__role { font-size: 21px; font-weight: 500; line-height: 30px; }

  .contacts {
    position: absolute;
    left: 438px;
    top: 234px;
    list-style: none;
  }
  .contacts__item {
    display: flex;
    align-items: center;
    height: 45px;
    font-size: 24px;
    color: var(--ink);
  }
  .contacts__icon {
    width: 20px;
    height: 20px;
    margin-right: 19px;
    flex: none;
  }

  .decoration {
    position: absolute;
    left: 43px;
    top: 53px;
    width: 314px;
    height: 372px;
    background:
      radial-gradient(ellipse 50% 48% at 50% 40%, var(--glow-top) 0%, var(--glow-mid) 55%, rgba(253,227,176,0) 100%),
      radial-gradient(ellipse 26% 30% at 50% 78%, var(--glow-bottom) 0%, rgba(253,227,176,0) 100%);
    opacity: 0.85;
  }
</style>
</head>
<body>
  <section class="card card--front" aria-label="Business card front">
    <div class="brand">
      <span class="brand__dot"></span>
      <div class="brand__text">
        <span class="brand__name">VALCORNE</span>
        <span class="brand__rule"></span>
        <span class="brand__tagline">HEALTH CARE MARKETING</span>
      </div>
    </div>
    <div class="divider"></div>
    <div class="person">
      <p class="person__name">Marla Tenwick</p>
      <p class="person__role">CEO</p>
    </div>
    <ul class="contacts">
      <li class="contacts__item">
        <svg class="contacts__icon" viewBox="0 0 20 20" aria-hidden="true">
          <rect width="20" height="20" rx="2" fill="#f08a24"/>
          <circle cx="10" cy="10" r="6" fill="none" stroke="#fff" stroke-width="1.6"/>
          <path d="M4 10h12M10 4c-3 3-3 9 0 12M10 4c3 3 3 9 0 12" fill="none" stroke="#fff" stroke-width="1.2"/>
        </svg>
        valcorne.com
      </li>
      <li class="contacts__item">
        <svg class="contacts__icon" viewBox="0 0 20 20" aria-hidden="true">
          <rect width="20" height="20" rx="2" fill="#f08a24"/>
          <path d="M4 8c0-2 3-3 6-3s6 1 6 3v1h-3V7.5H7V9H4z" fill="#fff"/>
          <rect x="6" y="10" width="8" height="5" rx="1" fill="#fff"/>
        </svg>
        #(512)638-2974
      </li>
      <li class="contacts__item">
        <svg class="contacts__icon" viewBox="0 0 20 20" aria-hidden="true">
          <rect width="20" height="20" rx="2" fill="#f08a24"/>
          <rect x="4" y="6" width="12" height="8" fill="#fff"/>
          <path d="M4 6l6 5 6-5" fill="none" stroke="#f08a24" stroke-width="1.2"/>
        </svg>
        marla@valcorne.com
      </li>
    </ul>
  </section>

  <section class="card card--back" aria-label="Business card back">
    <div class="decoration" role="img" aria-label="Large faint brand emblem in soft peach and gold tones"></div>
    <div class="brand">
      <span class="brand__dot"></span>
      <div class="brand__text">
        <span class="brand__name">VALCORNE</span>
        <span class="brand__rule"></span>
        <span class="brand__tagline">HEALTH CARE MARKETING</span>
      </div>
    </div>
  </section>
</body>
</html>
```